Trucking/service truck *Updated

Cards for a trucking company. Company transfers logs to saw mills. We are looking for something edgy, modern and fun. It's very limited when it comes to trucking business card choices. Plus the owner also runs an on-site service truck. He has 20+ years mechanic experience.
Colors are open. Favorites are orange & purple, but not must have. We really want to emphasize trust, dependability and knowledge with a bright, attention getter.
On card:
Fennimore & Fennimore
Dale Fennimore - Owner/Manager/Maintenance 555-214-0937
Tamra Fennimore -Office Administration/Bookkeeping 555-362-1748
4172 Maple Bend Rd.
Gilmer, Texas 70000
555-490-2613 - Office
Updates
Just a thought. Do you think you can combine the Taurus and Pisces signs? And put in the corner, or on the back or anything really? Thanks! You all or doing fantastic!

```html
<!DOCTYPE html>
<html lang="en">
<head>
<meta charset="utf-8">
<title>Fennimore &amp; Fennimore – Business Cards</title>
<link rel="stylesheet" href="https://fonts.googleapis.com/css2?family=Exo+2:wght@400;500;600&display=swap">
<style>
  :root {
    --bg: #e9e6e1;
    --card: #ffffff;
    --navy: #1f3f8f;
    --blue-deep: #1c3c8c;
    --blue-bright: #2f6fd6;
    --red: #e8352b;
    --ink: #3b3b3b;
    --ink-soft: #555555;
  }
  * { box-sizing: border-box; margin: 0; padding: 0; }
  html, body { width: 1200px; height: 903px; overflow: hidden; }
  body {
    background: var(--bg);
    font-family: "Exo 2", Arial, sans-serif;
    position: relative;
  }
  .card {
    position: absolute;
    width: 540px;
    height: 309px;
    background: var(--card);
    box-shadow: 0 6px 18px rgba(0,0,0,0.15);
    overflow: hidden;
  }
  .card--front { left: 40px; top: 297px; }
  .card--back  { left: 620px; top: 297px; }

  .brand {
    position: absolute;
    display: flex;
    align-items: center;
    gap: 10px;
    color: var(--navy);
    font-weight: 500;
    white-space: nowrap;
  }
  .brand__dot {
    width: 18px; height: 18px;
    border-radius: 50%;
    background: var(--blue-bright);
  }
  .card--front .brand { left: 50%; top: 50%; transform: translate(-50%, -50%); font-size: 26px; }
  .card--back .brand { left: 110px; top: 66px; font-size: 19px; }

  .corner-tab {
    position: absolute; left: 52px; top: 0;
    width: 56px; height: 30px;
    background: var(--navy);
  }
  .address {
    position: absolute; left: 34px; top: 140px;
    display: flex; gap: 8px;
    font-size: 12px; line-height: 1.45;
    color: var(--ink);
    white-space: nowrap;
  }
  .address svg { flex: none; margin-top: 1px; }

  .band {
    position: absolute; left: 300px; top: 108px;
    width: 240px; height: 30px;
    background: linear-gradient(90deg, var(--blue-deep), var(--blue-bright) 55%, var(--blue-deep));
  }
  .person { position: absolute; left: 300px; top: 148px; white-space: nowrap; }
  .person__name {
    color: var(--red); font-weight: 600;
    font-size: 19px; letter-spacing: 1.5px;
  }
  .person__title { color: var(--ink); font-size: 12.5px; margin-top: 2px; }

  .contacts {
    position: absolute; left: 252px; top: 198px;
    list-style: none;
    font-size: 11.5px; color: var(--ink-soft);
    white-space: nowrap;
  }
  .contacts li { display: flex; align-items: center; gap: 7px; height: 19px; }
  .contacts svg { flex: none; }
  .contacts__label { color: var(--ink); font-weight: 500; }
</style>
</head>
<body>

  <section class="card card--front" aria-label="Card front">
    <div class="brand"><span class="brand__dot"></span>Fennimore &amp; Fennimore</div>
  </section>

  <section class="card card--back" aria-label="Card back">
    <div class="corner-tab"></div>
    <div class="brand"><span class="brand__dot"></span>Fennimore &amp; Fennimore</div>

    <div class="address">
      <svg width="12" height="16" viewBox="0 0 12 16" aria-hidden="true">
        <path d="M6 0a6 6 0 0 0-6 6c0 4.5 6 10 6 10s6-5.5 6-10a6 6 0 0 0-6-6z" fill="var(--red)"/>
        <circle cx="6" cy="6" r="2.2" fill="#fff"/>
      </svg>
      <p>4172 Maple Bend Rd.<br>Gilmer, Texas 70000</p>
    </div>

    <div class="band"></div>
    <div class="person">
      <p class="person__name">DALE FENNIMORE</p>
      <p class="person__title">Owner / Manager / Maintenance</p>
    </div>

    <ul class="contacts">
      <li>
        <svg width="11" height="11" viewBox="0 0 12 12" aria-hidden="true"><path d="M2.5 0.5l2 2.5-1.2 1.5a7 7 0 0 0 4.2 4.2L9 7.5l2.5 2-1.5 2C5 11 1 7 0.5 2z" fill="var(--red)"/></svg>
        <span><span class="contacts__label">Dale</span> 555-214-0937</span>
      </li>
      <li>
        <svg width="11" height="11" viewBox="0 0 12 12" aria-hidden="true"><rect x="2.5" y="0.5" width="7" height="11" rx="1.2" fill="none" stroke="var(--red)" stroke-width="1.3"/></svg>
        <span><span class="contacts__label">Tamra</span> 555-362-1748</span>
      </li>
      <li>
        <svg width="11" height="11" viewBox="0 0 12 12" aria-hidden="true"><rect x="0.5" y="3" width="11" height="8" fill="var(--red)"/><rect x="2.5" y="0.5" width="7" height="3" fill="var(--red)"/></svg>
        <span><span class="contacts__label">Office</span> 555-490-2613</span>
      </li>
      <li>
        <svg width="11" height="11" viewBox="0 0 12 12" aria-hidden="true"><rect x="0.5" y="2" width="11" height="8" fill="var(--red)"/><path d="M1 2.5l5 4 5-4" fill="none" stroke="#fff" stroke-width="1"/></svg>
        office@fennimoretrucking.com
      </li>
      <li>
        <svg width="11" height="11" viewBox="0 0 12 12" aria-hidden="true"><circle cx="6" cy="6" r="5.5" fill="var(--red)"/><path d="M0.5 6h11M6 0.5c-3 3-3 8 0 11M6 0.5c3 3 3 8 0 11" fill="none" stroke="#fff" stroke-width="0.8"/></svg>
        www.fennimoretrucking.com
      </li>
    </ul>
  </section>

</body>
</html>
```